Law Firm in Texas in need of new letterhead

Law Firm in Fort Worth, TX, USA named "Pell & Varnum, Attorneys-At-Law, LLP." This is a general practice law firm that mostly does Family Law and Criminal Defense work.

We are looking for a new letterhead that has a "classical" appeal, with modern elements.

Any color combination is fine, but please note that we do fax many documents, so the design must be clearly legible in Black and White.

We would like our letterhead to project a sense of professionalism, integrity, and ability.

Target Market(s)

Letterhead will be for correspondence generally with other attorneys and clients.

Industry/Entity Type

Law Firm

Logo Text

Pell & Varnum, Attorneys-At-Law, LLP.

Logo styles of interest
Pictorial/Combination Logo
Wordmark Logo
Lettermark Logo
Requirements
Nice to have
• Although not necessary, a "Texas Star" that is incorporated into the design would be a nice touch.
Should not have
• Colors that do not convert to B&W easily

```html
<!DOCTYPE html>
<html lang="en">
<head>
<meta charset="utf-8">
<title>Pell &amp; Varnum Letterhead</title>
<link href="https://fonts.googleapis.com/css2?family=Oswald:wght@500&family=Krona+One&display=swap" rel="stylesheet">
<style>
  :root {
    --ink: #111111;
    --paper: #ffffff;
  }
  html, body {
    margin: 0;
    padding: 0;
    overflow: hidden;
    background: var(--paper);
  }
  .letterhead {
    position: relative;
    width: 840px;
    height: 1200px;
    background: var(--paper);
    overflow: hidden;
  }
  .brand-mark {
    position: absolute;
    left: 26px;
    top: 37px;
    width: 120px;
    height: 120px;
    border-radius: 50%;
    background: var(--ink);
  }
  .firm-name {
    position: absolute;
    left: 179px;
    top: 22px;
    margin: 0;
    font-family: 'Oswald', sans-serif;
    font-weight: 500;
    font-size: 31px;
    line-height: 1;
    letter-spacing: 0.6px;
    color: var(--ink);
    white-space: nowrap;
  }
  .rule-arrow {
    position: absolute;
    left: 170px;
    top: 56px;
    width: 646px;
    height: 12px;
  }
  .contact {
    position: absolute;
    left: 175px;
    top: 70px;
    margin: 0;
    padding: 0;
    list-style: none;
    font-family: 'Krona One', sans-serif;
    font-size: 17px;
    line-height: 22px;
    letter-spacing: 0.8px;
    color: var(--ink);
    white-space: nowrap;
  }
</style>
</head>
<body>
<main class="letterhead">
  <div class="brand-mark" aria-hidden="true"></div>
  <h1 class="firm-name">Pell &amp; Varnum, Attorneys-At-Law, LLP.</h1>
  <svg class="rule-arrow" viewBox="0 0 646 12" aria-hidden="true">
    <line x1="0" y1="6" x2="638" y2="6" stroke="var(--ink)" stroke-width="1.6"/>
    <polygon points="646,6 634,1.5 636,6 634,10.5" fill="var(--ink)"/>
  </svg>
  <ul class="contact">
    <li>Pell &amp; Varnum, Attorneys-at-Law, LP</li>
    <li>2140 E. Rosedale St.</li>
    <li>Fort Worth, TX 76111</li>
    <li>(817) 555-0142</li>
    <li>(817) 555-0187 (fax)</li>
  </ul>
</main>
</body>
</html>
```